Whitcombe Business Card Design

The name of the business is Dario Whitcombe, CPA LLC
The service that we offer is Accounting, Tax & Consulting Services. I need it to have the following items:
Dario Whitcombe, Principal
Phone Number
Email Address
Physical Address

I have attached the company logo, one in black and one in white. Please provide a design in black background and the other in white background. Please include "Accounting, Tax & Consulting Services". I want the business card to be clean and very professional.

```html
<!DOCTYPE html>
<html lang="en">
<head>
<meta charset="utf-8">
<title>Dario Whitcombe, CPA LLC – Business Card</title>
<link href="https://fonts.googleapis.com/css2?family=Montserrat:wght@600&family=Roboto:wght@400;500&display=swap" rel="stylesheet">
<style>
  :root {
    --page: #ffffff;
    --card: #ffffff;
    --card-edge: #e6e6e6;
    --crimson: #9b1b1f;
    --charcoal: #38383a;
    --ink: #222222;
  }
  html, body {
    margin: 0;
    padding: 0;
    width: 1200px;
    height: 896px;
    overflow: hidden;
    background: var(--page);
  }
  .canvas {
    position: relative;
    width: 1200px;
    height: 896px;
  }
  .card {
    position: absolute;
    left: 334px;
    width: 527px;
    height: 302px;
    background: var(--card);
    border: 1px solid var(--card-edge);
    border-radius: 26px;
    box-sizing: border-box;
  }
  .card--front { top: 125px; }
  .card--back { top: 472px; }

  /* front */
  .brand-block {
    position: absolute;
    left: 20px;
    width: 250px;
    top: 110px;
    text-align: center;
  }
  .brand-square {
    width: 24px;
    height: 24px;
    background: var(--charcoal);
    margin: 0 auto 14px;
  }
  .brand-name {
    font-family: "Montserrat", sans-serif;
    font-weight: 600;
    font-size: 13px;
    color: var(--charcoal);
    letter-spacing: 0.2px;
    white-space: nowrap;
  }
  .divider {
    position: absolute;
    left: 280px;
    top: 79px;
    width: 2px;
    height: 145px;
    background: var(--crimson);
  }
  .contact {
    position: absolute;
    left: 287px;
    top: 73px;
    font-family: "Roboto", sans-serif;
    color: var(--ink);
  }
  .contact__name {
    font-weight: 500;
    font-size: 21px;
    color: var(--crimson);
    line-height: 24px;
    margin: 0;
  }
  .contact__title {
    font-size: 12.5px;
    line-height: 16px;
    margin: 0 0 20px;
  }
  .contact__line {
    font-size: 12.5px;
    line-height: 20px;
    margin: 0;
    display: flex;
    align-items: center;
    gap: 3px;
  }
  .contact__gap { height: 10px; }
  .contact__line svg { width: 12px; height: 12px; fill: var(--crimson); }
  .services {
    position: absolute;
    left: 0;
    right: 0;
    top: 264px;
    text-align: center;
    font-family: "Roboto", sans-serif;
    font-size: 12.5px;
    color: var(--ink);
  }

  /* back */
  .back-square {
    position: absolute;
    left: 228px;
    top: 70px;
    width: 70px;
    height: 70px;
    background: var(--charcoal);
  }
  .back-name {
    position: absolute;
    left: 0;
    right: 0;
    top: 172px;
    text-align: center;
    font-family: "Montserrat", sans-serif;
    font-weight: 600;
    font-size: 29px;
    color: var(--charcoal);
    white-space: nowrap;
  }
</style>
</head>
<body>
<div class="canvas">

  <section class="card card--front">
    <div class="brand-block">
      <div class="brand-square"></div>
      <div class="brand-name">Dario Whitcombe, CPA LLC</div>
    </div>
    <div class="divider"></div>
    <div class="contact">
      <p class="contact__name">Dario Whitcombe</p>
      <p class="contact__title">Principal</p>
      <p class="contact__line">Physical Address</p>
      <p class="contact__line">Cove Harbor CA 92600</p>
      <div class="contact__gap"></div>
      <p class="contact__line">
        <svg viewBox="0 0 24 24" aria-hidden="true"><path d="M6.6 10.8a15.1 15.1 0 0 0 6.6 6.6l2.2-2.2c.3-.3.7-.4 1-.2 1.1.4 2.3.6 3.6.6.6 0 1 .4 1 1V20c0 .6-.4 1-1 1A17 17 0 0 1 3 4c0-.6.4-1 1-1h3.5c.6 0 1 .4 1 1 0 1.3.2 2.5.6 3.6.1.3 0 .7-.2 1z"/></svg>
        555 014 272
      </p>
      <p class="contact__line">
        <svg viewBox="0 0 24 24" aria-hidden="true"><path d="M2 5h20v14H2z" opacity=".9"/><path d="M2 5l10 7 10-7" fill="none" stroke="#fff" stroke-width="2"/></svg>
        info@whitcombecpa.com
      </p>
    </div>
    <div class="services">Accounting, Tax &amp; Consulting Services</div>
  </section>

  <section class="card card--back">
    <div class="back-square"></div>
    <div class="back-name">Dario Whitcombe, CPA LLC</div>
  </section>

</div>
</body>
</html>
```